Harbor Loom Floors Letterhead

Letterhead used for business reasons. It must be editable and easy to use.

Address is 2715 W. Pelican Lane Englewood FL 34187 - 941.382.6519

```html
<!DOCTYPE html>
<html lang="en">
<head>
<meta charset="utf-8">
<title>Harbor Loom Floors Letterhead</title>
<link href="https://fonts.googleapis.com/css2?family=Source+Sans+3:wght@400&family=Montserrat:wght@400&display=swap" rel="stylesheet">
<style>
  :root {
    --backdrop: #e4e4e4;
    --paper: #ffffff;
    --brand-orange: #e08a22;
    --ink-navy: #1e2b4d;
    --ink-body: #4a4a4a;
    --ink-footer: #2b2b2b;
    --signature-tone: #b5b5b5;
  }
  * { margin: 0; padding: 0; box-sizing: border-box; }
  html, body {
    width: 1200px; height: 1079px; overflow: hidden;
    background: var(--backdrop);
  }
  .letterhead {
    position: absolute; left: 232px; top: 20px;
    width: 735px; height: 1039px;
    background: var(--paper);
    font-family: "Source Sans 3", sans-serif;
    color: var(--ink-body);
    overflow: hidden;
  }
  .brand-name {
    position: absolute; left: 73px; top: 46px;
    font-size: 46px; line-height: 1.1; font-weight: 400;
    color: var(--brand-orange);
  }
  .salutation {
    position: absolute; left: 73px; top: 318px;
    font-size: 17.5px; color: var(--ink-navy);
  }
  .letter-body {
    position: absolute; left: 73px; top: 390px; width: 590px;
    font-size: 13px; line-height: 14.7px; text-align: justify;
    text-align-last: left;
  }
  .letter-body p { margin-bottom: 29px; }
  .closing {
    position: absolute; left: 73px; top: 717px;
    font-size: 13px;
  }
  .signature {
    position: absolute; left: 73px; top: 738px;
    width: 61px; height: 10px;
  }
  .signer-name {
    position: absolute; left: 73px; top: 762px;
    font-size: 13px; text-transform: uppercase;
  }
  .contact-footer {
    position: absolute; left: 0; top: 942px; width: 100%;
    font-family: "Montserrat", sans-serif; color: var(--ink-footer);
    font-size: 12.5px; line-height: 16px; text-align: center;
  }
  .contact-phone { display: flex; justify-content: center; align-items: center; gap: 5px; }
  .contact-rule { width: 285px; height: 1.5px; background: var(--brand-orange); margin: 6px auto 5px; }
  .contact-address { white-space: nowrap; }
</style>
</head>
<body>
<main class="letterhead">
  <div class="brand-name">Harbor Loom<br>Floors</div>

  <p class="salutation">Dear Mr. Alden</p>

  <section class="letter-body">
    <p>Lorem Ipsum is simply dummy text of the printing and typesetting industry. Lorem Ipsum has been the industry's standard dummy text ever since the 1500s, when an unknown printer took a galley of type and scrambled it to make a type specimen book. It has survived not only five centuries, but also the leap into electronic typesetting, remaining essentially unchanged. It was popularised in the 1960s with the release of Letraset sheets containing Lorem Ipsum passages</p>
    <p>Lorem Ipsum is simply dummy text of the printing and typesetting industry. Lorem Ipsum has been the industry's standard dummy text ever since the 1500s, when an unknown printer took a galley of type and scrambled it to make a type specimen book. It has survived not only five centuries, but also the leap into electronic typesetting, remaining essentially unchanged. It was popularised in the 1960s with the release of Letraset sheets containing Lorem Ipsum passages</p>
    <p>Lorem Ipsum is simply dummy text of the printing and typesetting industry. Lorem Ipsum has been the industry's standard dummy text ever since the 1500s, when an unknown printer took a galley of type and scrambled it to make a type specimen book. It has survived not only five centuries, but also the leap into electronic typesetting, remaining essentially unchanged. It was popularised in the 1960s with the release of Letraset sheets containing Lorem Ipsum passages</p>
  </section>

  <p class="closing">Siccaely</p>
  <svg class="signature" role="img" aria-label="Handwritten signature of Nora Whitfield" viewBox="0 0 61 10">
    <rect x="0" y="4" width="61" height="3" rx="1.5" fill="var(--signature-tone)" opacity="0.6"/>
  </svg>
  <p class="signer-name">Nora Whitfield</p>

  <footer class="contact-footer">
    <div class="contact-phone">
      <svg width="11" height="11" viewBox="0 0 24 24" aria-hidden="true">
        <path fill="var(--brand-orange)" d="M6.6 10.8a15.1 15.1 0 0 0 6.6 6.6l2.2-2.2a1 1 0 0 1 1-.25 11.4 11.4 0 0 0 3.6.57 1 1 0 0 1 1 1V20a1 1 0 0 1-1 1A17 17 0 0 1 3 4a1 1 0 0 1 1-1h3.5a1 1 0 0 1 1 1c0 1.250.2 2.450.57 3.570a1 1 0 0 1-.25 1z"/>
      </svg>
      <span>941.382.6519</span>
    </div>
    <div class="contact-rule"></div>
    <div class="contact-address">2715 W. Pelican Lane Englewood FL 34187</div>
  </footer>
</main>
</body>
</html>
```